Business Card Design for Occupational Medicine Start Up Company

We need to design a professional business card. We are a healthcare company providing occupational medicine services to blue collar industries. We are professional, efficient and high quality service providers.

Target Market(s)

Blue Collar Industry: Shipbuilding, Ports, Trucking Companies; The Executives and Safety Officers for these companies

Industry/Entity Type

Healthcare

Contact Information for Business Card

Logo, Name, Title, Email, Phone

Other font styles liked:
• Please match our Brand Guide

Requirements
Must have
• Our Company Colors and Logo

```html
<!DOCTYPE html>
<html lang="en">
<head>
<meta charset="utf-8">
<title>CrewGuard Clinics – Business Card</title>
<link href="https://fonts.googleapis.com/css2?family=Montserrat:wght@400;700&display=swap" rel="stylesheet">
<style>
  :root{
    --backdrop:#2b2b2d;
    --brand-navy:#283a88;
    --brand-orange:#f2b04c;
    --brand-sky:#29a9e1;
    --paper:#ffffff;
    --ink-grey:#6d6e71;
  }
  *{margin:0;padding:0;box-sizing:border-box}
  html,body{width:1200px;height:1024px;overflow:hidden}
  body{background:var(--backdrop);font-family:"Montserrat",Arial,sans-serif;position:relative}
  .card{position:absolute;left:220px;width:760px;height:434px;overflow:hidden;box-shadow:0 12px 30px rgba(0,0,0,.45)}
  .card--front{top:60px;background:var(--brand-navy);display:flex;align-items:center;justify-content:center}
  .card--back{top:530px;background:var(--paper)}
  .wordmark{display:flex;align-items:center;gap:16px;font-weight:700;letter-spacing:.04em;text-transform:uppercase;line-height:1.1}
  .wordmark__text{display:flex;flex-direction:column}
  .wordmark__dot{width:22px;height:22px;border-radius:50%;background:var(--brand-orange);flex:none}
  .card--front .wordmark{color:var(--paper);font-size:40px}
  .card--back .wordmark{position:absolute;left:70px;top:110px;color:var(--brand-navy);font-size:32px}
  .name-band{position:absolute;left:470px;top:0;width:200px;height:250px;background:var(--brand-navy);color:var(--paper);text-align:center;padding-top:46px}
  .name-band__name{font-weight:700;font-size:20px;letter-spacing:.03em}
  .name-band__title{font-weight:400;font-size:14px;margin-top:2px}
  .corner-mark{position:absolute;left:485px;top:190px;width:170px;height:170px;border-radius:50%;background:var(--brand-sky);border:8px solid var(--paper)}
  .contact{position:absolute;left:70px;bottom:48px;list-style:none;color:var(--ink-grey);font-size:17px}
  .contact li{display:flex;align-items:center;gap:12px;margin-top:8px}
  .contact__icon{width:20px;height:20px;border-radius:50%;background:var(--brand-orange);display:flex;align-items:center;justify-content:center;flex:none}
</style>
</head>
<body>
  <section class="card card--front">
    <div class="wordmark"><span class="wordmark__dot"></span><span class="wordmark__text"><span>CrewGuard</span><span>Clinics</span></span></div>
  </section>

  <section class="card card--back">
    <div class="wordmark"><span class="wordmark__dot"></span><span class="wordmark__text"><span>CrewGuard</span><span>Clinics</span></span></div>

    <div class="name-band">
      <p class="name-band__name">DANIEL REYES</p>
      <p class="name-band__title">Manage</p>
    </div>
    <div class="corner-mark"></div>

    <ul class="contact">
      <li>
        <span class="contact__icon"><svg width="11" height="11" viewBox="0 0 24 24"><path fill="#fff" d="M6.6 10.8a15 15 0 0 0 6.6 6.6l2.2-2.2c.3-.3.7-.4 1-.2 1.1.4 2.3.6 3.6.6.6 0 1 .4 1 1V20c0 .6-.4 1-1 1A17 17 0 0 1 3 4c0-.6.4-1 1-1h3.5c.6 0 1 .4 1 1 0 1.3.2 2.5.6 3.6.1.3 0 .7-.2 1z"/></svg></span>
        555-010-200
      </li>
      <li>
        <span class="contact__icon"><svg width="11" height="11" viewBox="0 0 24 24"><path fill="#fff" d="M3 5h18v14H3z"/><path fill="none" stroke="#f2b04c" stroke-width="2" d="M3 6l9 7 9-7"/></svg></span>
        info@crewguardclinics.com
      </li>
      <li>
        <span class="contact__icon"><svg width="11" height="11" viewBox="0 0 24 24"><path fill="#fff" d="M12 2a7 7 0 0 0-7 7c0 5 7 13 7 13s7-8 7-13a7 7 0 0 0-7-7zm0 9.5A2.5 2.5 0 1 1 12 6.5a2.5 2.5 0 0 1 0 5z"/></svg></span>
        Your address, your city, box 88900
      </li>
    </ul>
  </section>
</body>
</html>
```